OrvanoGoodsHub.com -Ecommerce Website for Luxury Products

This will be an ecommerce site. A website portal that will allow both consumers to enter one way and see specific purchase options and businesses to enter via a different link that allows B2B to see their specific options once logged into. B2C can purchase both as a guest/or after account is setup. B2B must be approved to set up account. This is front end website project. Back-end integration is separate. Will be hosted on Servantia with a domain registration held at Pexadrinet. Additional website concept/idea/synergy can be found from sister site-KRWZHospitality.com

```html
<!DOCTYPE html>
<html lang="en">
<head>
<meta charset="utf-8">
<title>OrvanoGoods – Luxury Lifestyle Accoutrements</title>
<link rel="stylesheet" href="https://fonts.googleapis.com/css2?family=Cinzel:wght@400;600;700&family=Nunito+Sans:wght@400;600&display=swap">
<style>
:root{
  --ink:#111111;
  --cream:#faf6f2;
  --white:#ffffff;
  --muted:#3a3a3a;
  --gold:#f2a81d;
  --line:#cfcfcf;
  --footer:#000000;
}
*{box-sizing:border-box;margin:0;padding:0}
html,body{width:1200px;height:3336px;overflow:hidden}
body{font-family:"Nunito Sans",Arial,sans-serif;color:var(--ink);background:var(--white);position:relative}
.serif{font-family:"Cinzel",Georgia,serif}
.wrap{position:relative;width:980px;margin:0 auto}

/* header */
.topbar{height:104px;position:relative}
.search{position:absolute;left:110px;top:30px;width:296px;height:42px;border:1px solid #9a9a9a;display:flex;align-items:center;padding:0 16px;font-size:15px;color:#333;justify-content:space-between}
.brand{position:absolute;left:50%;transform:translateX(-50%);top:14px;text-align:center}
.brand-mark{width:22px;height:22px;border:2px solid var(--ink);border-radius:50%;margin:0 auto 6px}
.brand-name{font-family:"Cinzel",Georgia,serif;font-size:22px;letter-spacing:1px;line-height:1}
.brand-sub{font-size:7px;letter-spacing:1.2px;font-weight:600;margin-top:3px}
.account{position:absolute;right:110px;top:38px;display:flex;align-items:center;gap:14px;font-size:15px}
.account svg{width:24px;height:24px}
.nav{height:46px;background:var(--cream);display:flex;align-items:center;padding-left:112px;gap:0}
.nav a{font-family:"Cinzel",Georgia,serif;font-size:15px;color:var(--ink);text-decoration:none;margin-right:48px;letter-spacing:.3px}
.nav a.active{font-weight:700}

/* hero */
.hero{height:585px;position:relative;background:radial-gradient(ellipse at 50% 55%,#5a2418 0%,#2b130c 45%,#0f0805 100%);color:var(--white);text-align:center}
.hero h1{font-family:"Cinzel",Georgia,serif;font-weight:700;font-size:47px;line-height:53px;padding-top:172px;letter-spacing:.5px}
.hero p{font-family:"Cinzel",Georgia,serif;font-weight:600;font-size:18px;margin-top:18px}
.btn-light{display:inline-block;background:var(--white);color:var(--ink);border-radius:30px;padding:12px 28px;font-family:"Cinzel",Georgia,serif;font-weight:700;font-size:17px;margin-top:18px}
.scroll{position:absolute;left:50%;top:478px;transform:translateX(-50%)}

/* sections */
.title{text-align:center;font-family:"Cinzel",Georgia,serif;font-weight:600;font-size:36px;letter-spacing:1px}
.title::after{content:"";display:block;width:54px;height:3px;background:var(--ink);margin:10px auto 0}
.arrow{position:absolute;top:50%;transform:translateY(-50%)}
.collections{padding-top:96px;height:541px}
.row{display:flex;gap:22px;margin-top:32px;position:relative;width:980px;margin-left:auto;margin-right:auto}
.coll{width:228px;text-align:center}
.coll .img{height:233px;border-radius:6px}
.coll h3{font-family:"Cinzel",Georgia,serif;font-weight:600;font-size:16px;margin-top:20px}

.about{height:508px;display:flex;background:var(--cream)}
.about-text{width:600px;padding:80px 0 0 110px}
.about-text h2{font-family:"Cinzel",Georgia,serif;font-weight:600;font-size:38px}
.about-text h2::after{content:"";display:block;width:60px;height:3px;background:var(--ink);margin-top:6px}
.about-text p{font-size:14.5px;line-height:26px;color:var(--muted);margin-top:22px;width:440px}
.btn-outline{display:inline-block;border:2px solid var(--ink);border-radius:28px;padding:11px 22px;font-family:"Cinzel",Georgia,serif;font-weight:700;font-size:17px;margin-top:22px}
.about-img{width:600px;height:508px;background:radial-gradient(circle at 60% 60%,#a2642a 0%,#5a3518 35%,#1e140c 80%)}

.products{padding-top:106px;height:650px;position:relative}
.prod{width:228px;position:relative;height:300px}
.prod .img{height:246px;background:var(--cream);border-radius:6px}
.prod .card{position:absolute;left:14px;right:14px;top:182px;background:var(--white);box-shadow:0 2px 10px rgba(0,0,0,.1);border-radius:4px;text-align:center;padding:18px 6px 16px}
.prod h3{font-family:"Cinzel",Georgia,serif;font-weight:600;font-size:15.5px;line-height:20px}
.price{font-family:"Cinzel",Georgia,serif;font-weight:600;font-size:16px;margin-top:8px}
.stars{color:var(--gold);font-size:15px;letter-spacing:-1px;margin-top:4px}
.prod.hover .card{border-bottom:3px solid var(--ink)}
.btn-dark{display:inline-block;background:var(--ink);color:var(--white);border-radius:14px;padding:5px 13px;font-family:"Cinzel",Georgia,serif;font-weight:700;font-size:11px;margin-top:10px}

.partners{height:473px;background:var(--cream);padding-top:88px}
.pgrid{display:flex;gap:52px;width:980px;margin:42px auto 0}
.partner{display:flex;gap:20px;width:464px}
.partner .img{width:215px;height:206px;flex:none}
.partner h3{font-family:"Cinzel",Georgia,serif;font-weight:600;font-size:16px;line-height:25px;margin-top:2px}
.partner p{font-size:14px;line-height:24px;color:var(--muted);margin-top:4px}
.plogo{font-family:"Nunito Sans",Arial,sans-serif;font-weight:600;font-size:28px;margin-top:6px}

.footer{height:429px;background:var(--footer);color:var(--white);position:relative}
.fcol{position:absolute;top:62px}
.fcol h4{font-family:"Cinzel",Georgia,serif;font-weight:600;font-size:19px;margin-bottom:14px}
.fcol li{list-style:none;font-size:15px;line-height:31px;display:flex;align-items:center;gap:10px}
.contact li{line-height:60px;gap:14px}
.ico{width:36px;height:36px;border-radius:50%;background:var(--white);display:flex;align-items:center;justify-content:center}
.newsletter p{font-size:15px;line-height:31px;width:290px}
.email{border-bottom:2px solid var(--white);width:272px;padding:8px 2px;font-size:15px;margin-top:4px}
.fbtn{display:inline-block;background:var(--white);color:var(--ink);border-radius:28px;padding:14px 24px;font-family:"Cinzel",Georgia,serif;font-weight:700;font-size:17px;margin-top:26px}
.copy{position:absolute;left:98px;right:98px;top:366px;border-top:1px solid #777;text-align:center;padding-top:16px;font-size:15px}
</style>
</head>
<body>

<header class="topbar">
  <div class="search">Search
    <svg width="16" height="16" viewBox="0 0 16 16" fill="none" stroke="#333" stroke-width="1.5"><circle cx="7" cy="7" r="5"/><path d="M11 11l4 4"/></svg>
  </div>
  <div class="brand">
    <div class="brand-mark"></div>
    <div class="brand-name">ORVANOGOODS</div>
    <div class="brand-sub">A DIVISION OF KRWZ HOSPITALITY</div>
  </div>
  <div class="account">
    <span>Log In &nbsp;|&nbsp; Sign Up</span>
    <svg viewBox="0 0 24 24" fill="none" stroke="#111" stroke-width="1.6"><path d="M12 20s-8-5-8-11a4 4 0 018-1 4 4 0 018 1c0 6-8 11-8 11z"/></svg>
    <svg viewBox="0 0 24 24" fill="none" stroke="#111" stroke-width="1.6"><path d="M5 8h14l-1 13H6z"/><path d="M9 8V6a3 3 0 016 0v2"/></svg>
    <svg viewBox="0 0 24 24" fill="none" stroke="#111" stroke-width="1.4"><circle cx="12" cy="12" r="9"/><path d="M3 12h18M12 3c3 3 3 15 0 18M12 3c-3 3-3 15 0 18"/></svg>
  </div>
</header>

<nav class="nav">
  <a class="active">HOME</a><a>ABOUT US</a><a>RETAIL COLLECTIONS</a><a>WHOLESALE PORTAL</a><a>PARTNER</a><a>CONTACT &amp; CONCIERGE</a>
</nav>

<section class="hero" role="img" aria-label="Dim lounge with red leather chesterfield sofas, warm lamps and a stocked bar">
  <h1>PURVEYORS OF<br>LUXURY LIFESTYLE ACCOUTREMENTS</h1>
  <p>Curating limited edition luxury items is fun... but one of a kind is LUXE.</p>
  <span class="btn-light">Shop Now</span>
  <svg class="scroll" width="26" height="58" viewBox="0 0 26 58" fill="none" stroke="#fff" stroke-width="2"><rect x="2" y="2" width="22" height="36" rx="11"/><path d="M13 10v8M13 44v12M8 51l5 5 5-5"/></svg>
</section>

<section class="collections">
  <h2 class="title">FEATURED COLLECTIONS</h2>
  <div class="row">
    <svg class="arrow" style="left:-66px;top:150px" width="16" height="26" viewBox="0 0 16 26" fill="none" stroke="#111" stroke-width="2"><path d="M14 2L3 13l11 11"/></svg>
    <div class="coll"><div class="img" role="img" aria-label="Whisky glass and cigar on a dark table" style="background:linear-gradient(135deg,#3a2010,#8a4a1c 60%,#2a160a)"></div><h3>CIGAR ACCESSORIES</h3></div>
    <div class="coll"><div class="img" role="img" aria-label="Aroma diffuser with essential oil bottles" style="background:linear-gradient(135deg,#c9a36a,#7a4a20 55%,#3a2a1c)"></div><h3>OILS</h3></div>
    <div class="coll"><div class="img" role="img" aria-label="Perfume bottle on dark stones" style="background:linear-gradient(135deg,#2a2a2a,#6a6a66 55%,#1a1a1a)"></div><h3>FRAGRANCES</h3></div>
    <div class="coll"><div class="img" role="img" aria-label="Tan leather jacket and backpack in a boutique" style="background:linear-gradient(135deg,#e8ddd4,#b86a3a 55%,#d9cbbf)"></div><h3>ATTIRE &amp; ACCESSORIES</h3></div>
    <svg class="arrow" style="right:-66px;top:150px" width="16" height="26" viewBox="0 0 16 26" fill="none" stroke="#111" stroke-width="2"><path d="M2 2l11 11L2 24"/></svg>
  </div>
</section>

<section class="about">
  <div class="about-text">
    <h2>About Us</h2>
    <p>Lorem ipsum dolor sit amet, consectetur adipiscing elit, sed do eiusmod tempor incididunt ut labore et dolore magna aliqua. Ut enim ad minim veniam, quis nostrud exercitation ullamco laboris nisi ut aliquip ex ea commodo consequat.</p>
    <p>Duis aute irure dolor in reprehenderit in voluptate velit esse cillum dolore eu fugiat nulla pariatur. Excepteur sint occaecat cupidatat non proident, sunt in culpa qui officia deserunt laborum.</p>
    <span class="btn-outline">READ MORE</span>
  </div>
  <div class="about-img" role="img" aria-label="Glass of whisky and cigar on a table in a warmly lit cigar lounge"></div>
</section>

<section class="products">
  <h2 class="title">FEATURED PRODUCTS</h2>
  <div class="row">
    <svg class="arrow" style="left:-66px;top:150px" width="16" height="26" viewBox="0 0 16 26" fill="none" stroke="#111" stroke-width="2"><path d="M14 2L3 13l11 11"/></svg>
    <div class="prod"><div class="img" role="img" aria-label="Ornate silver cigarette case"></div><div class="card"><h3>CIGAR ACCESSORIES</h3><div class="price">$45.00</div><div class="stars">★★★★★</div></div></div>
    <div class="prod"><div class="img" role="img" aria-label="Clear perfume bottle"></div><div class="card"><h3>FRAGRANCES</h3><div class="price">$45.00</div><div class="stars">★★★★★</div></div></div>
    <div class="prod hover"><div class="img" role="img" aria-label="Grey t-shirt, white sneakers and black trousers"></div><div class="card"><h3>ATTIRE AND<br>ACCESSORIES</h3><div class="price">$45.00</div><div class="stars">★★★★★</div><span class="btn-dark">SHOP NOW</span></div></div>
    <div class="prod"><div class="img" role="img" aria-label="Ornate silver cigarette case"></div><div class="card"><h3>CIGAR ACCESSORIES</h3><div class="price">$45.00</div><div class="stars">★★★★★</div></div></div>
    <svg class="arrow" style="right:-66px;top:150px" width="16" height="26" viewBox="0 0 16 26" fill="none" stroke="#111" stroke-width="2"><path d="M2 2l11 11L2 24"/></svg>
  </div>
</section>

<section class="partners">
  <h2 class="title">OUR PARTNER</h2>
  <div class="pgrid">
    <div class="partner">
      <div class="img" role="img" aria-label="Man relaxing in a leather armchair with a cigar" style="background:linear-gradient(135deg,#2a1a10,#8a5a30 60%,#1a100a)"></div>
      <div><h3>LOREM IPSUM DOLOR SIT AMET, CONSECTETUR ADIPISCING ELIT</h3><p>Excepteur sint occaecat cupidatat non proident, sunt in mollit anim id est laborum.</p><div class="plogo">Velmora</div></div>
    </div>
    <div class="partner">
      <div class="img" role="img" aria-label="Brandy glass and cigars on a wooden box in a library" style="background:linear-gradient(135deg,#1a120c,#9a5a24 55%,#3a2414)"></div>
      <div><h3>LOREM IPSUM DOLOR SIT AMET, CONSECTETUR ADIPISCING ELIT</h3><p>Excepteur sint occaecat cupidatat non proident, sunt in mollit anim id est laborum.</p><div class="plogo">Ostrel</div></div>
    </div>
  </div>
</section>

<footer class="footer">
  <div class="fcol" style="left:97px">
    <h4>Quick Links</h4>
    <ul>
      <li>➔ Home</li><li>➔ About Us</li><li>➔ Retail Collections</li><li>➔ Wholesale Portal</li><li>➔ Partner</li><li>➔ Contact &amp; Concierge</li>
    </ul>
  </div>
  <div class="fcol" style="left:324px">
    <h4>Other Links</h4>
    <ul>
      <li>➔ FAQ</li><li>➔ Tems of Use</li><li>➔ Privacy Policy</li><li>➔ Support Links</li><li>➔ Conditions</li>
    </ul>
  </div>
  <div class="fcol contact" style="left:525px">
    <h4>Contact Us</h4>
    <ul style="margin-top:-8px">
      <li><span class="ico"><svg width="14" height="16" viewBox="0 0 14 16"><path d="M7 0a6 6 0 016 6c0 4-6 10-6 10S1 10 1 6a6 6 0 016-6z" fill="#111"/><circle cx="7" cy="6" r="2" fill="#fff"/></svg></span>Company Name, United State.</li>
      <li><span class="ico"><svg width="16" height="12" viewBox="0 0 16 12"><rect width="16" height="12" rx="1" fill="#111"/><path d="M1 1l7 6 7-6" stroke="#fff" fill="none"/></svg></span>info@orvanogoods.example</li>
      <li><span class="ico"><svg width="14" height="14" viewBox="0 0 14 14"><path d="M3 0l3 3-2 2a8 8 0 005 5l2-2 3 3-2 3C6 14 0 8 0 2z" fill="#111"/></svg></span>+1 555 0142 7788</li>
    </ul>
  </div>
  <div class="fcol newsletter" style="left:829px">
    <h4>Sign Up To Our Newsletter</h4>
    <p>Lorem ipsum dolor sit amet,consectetur adipiscing elit,adipiscing elit.</p>
    <div class="email">Email</div>
    <span class="fbtn">Subscribe</span>
  </div>
  <div class="copy">Copyrights@2026.Company Name.All Rights Reserved</div>
</footer>

</body>
</html>
```